design a construction company business card

Design business card around our logo. Card must have all the typical info: name, title, address, phone, email, business name, etc. Somewhere on the card I would like to see our motto "Built on integrity... Inspired by commitment." Consider adding a splash of bright orange to the card to complement the blues and silvers/grays in the logo. We are open to metallic inks, textures, etc. We would like to see options on both light and dark backgrounds. The font in the logo is Euro Technic Extended Regular.

```html
<!DOCTYPE html>
<html lang="en">
<head>
<meta charset="utf-8">
<title>Halden Contracting – Business Card</title>
<link href="https://fonts.googleapis.com/css2?family=Roboto:ital,wght@0,400;0,500;0,700;1,400&display=swap" rel="stylesheet">
<style>
  :root {
    --page: #e4e4e4;
    --paper: #ffffff;
    --blue-deep: #283f98;
    --blue-mid: #1f55ad;
    --blue-bright: #1a72bd;
    --gray-tab: #808285;
    --gray-text: #4a4a4a;
    --silver: #d3d6da;
    --white: #ffffff;
  }
  * { box-sizing: border-box; margin: 0; padding: 0; }
  html, body { width: 1125px; height: 1200px; overflow: hidden; }
  body {
    background: var(--page);
    font-family: "Roboto", Arial, sans-serif;
    position: relative;
  }
  .card {
    position: absolute;
    left: 171px;
    width: 826px;
    height: 472px;
    overflow: hidden;
  }
  .card--front { top: 106px; background: var(--paper); }
  .card--back {
    top: 639px;
    background: radial-gradient(ellipse at 50% 45%, var(--blue-bright) 0%, var(--blue-mid) 45%, var(--blue-deep) 100%);
  }

  /* Front: brand */
  .brand {
    position: absolute;
    left: 470px;
    top: 108px;
    display: flex;
    align-items: center;
    gap: 12px;
  }
  .brand__square { width: 22px; height: 22px; background: var(--blue-mid); }
  .brand__name {
    font-weight: 700;
    font-size: 25px;
    letter-spacing: 1px;
    color: var(--blue-mid);
    text-transform: uppercase;
  }

  /* Front: name tab */
  .name-tab {
    position: absolute;
    left: 0; top: 253px;
    width: 367px; height: 78px;
    background: var(--gray-tab);
    clip-path: polygon(0 0, 303px 0, 367px 100%, 0 100%);
    padding: 12px 0 0 52px;
    color: var(--white);
  }
  .name-tab__name { font-weight: 700; font-size: 30px; line-height: 1.1; }
  .name-tab__title { font-weight: 500; font-size: 20px; line-height: 1.2; }

  /* Front: contact band */
  .contact-band {
    position: absolute;
    left: 0; top: 335px;
    width: 100%; height: 137px;
    background: linear-gradient(90deg, var(--blue-deep) 0%, var(--blue-bright) 55%, var(--blue-deep) 100%);
    color: var(--white);
    font-size: 19.5px;
  }
  .contact-list { position: absolute; left: 52px; top: 30px; list-style: none; }
  .contact-list li { display: flex; align-items: center; gap: 12px; height: 26px; }
  .contact-list svg { width: 17px; height: 17px; fill: var(--white); }
  .address {
    position: absolute; right: 50px; top: 30px;
    text-align: right; font-style: normal; line-height: 26px;
  }
  .web-strip {
    position: absolute; right: 0; bottom: 0;
    width: 372px; height: 41px;
    background: var(--paper);
    clip-path: polygon(35px 0, 100% 0, 100% 100%, 0 100%);
    text-align: right;
    padding: 7px 50px 0 0;
    color: var(--gray-text);
    font-size: 18px;
    letter-spacing: 3.6px;
  }

  /* Back */
  .back-brand {
    position: absolute;
    left: 0; right: 0; top: 220px;
    text-align: center;
    font-weight: 700;
    font-size: 34px;
    letter-spacing: 2px;
    color: var(--silver);
    text-transform: uppercase;
  }
  .back-rule {
    position: absolute; left: 222px; width: 382px; top: 330px;
    height: 7px; background: var(--silver);
  }
  .motto {
    position: absolute; left: 0; right: 0; top: 343px;
    text-align: center;
    font-style: italic;
    font-size: 19.5px;
    color: var(--white);
  }
</style>
</head>
<body>
  <section class="card card--front" aria-label="Business card front">
    <div class="brand">
      <span class="brand__square"></span>
      <span class="brand__name">Halden Contracting, Inc.</span>
    </div>

    <div class="name-tab">
      <p class="name-tab__name">MARK ELLISON</p>
      <p class="name-tab__title">CEO/FOUNDER</p>
    </div>

    <div class="contact-band">
      <ul class="contact-list">
        <li>
          <svg viewBox="0 0 24 24" aria-hidden="true"><path d="M6.6 10.8a15.1 15.1 0 0 0 6.6 6.6l2.2-2.2a1 1 0 0 1 1-.25 11.4 11.4 0 0 0 3.6.57 1 1 0 0 1 1 1V20a1 1 0 0 1-1 1A17 17 0 0 1 3 4a1 1 0 0 1 1-1h3.5a1 1 0 0 1 1 1c0 1.25.2 2.45.57 3.57a1 1 0 0 1-.25 1z"/></svg>
          555 210 4876
        </li>
        <li>
          <svg viewBox="0 0 24 24" aria-hidden="true"><path d="M2 5h20v14H2z M3.5 6.5 12 13l8.5-6.5" fill="var(--white)" stroke="var(--blue-deep)" stroke-width="1.6"/></svg>
          info@haldenbuild.com
        </li>
      </ul>
      <address class="address">1420 Cedar Ridge Road<br>Anchorage, Alaska 99508</address>
      <div class="web-strip">www.haldenbuild.com</div>
    </div>
  </section>

  <section class="card card--back" aria-label="Business card back">
    <p class="back-brand">Halden Contracting, Inc.</p>
    <div class="back-rule"></div>
    <p class="motto">Built on integrity... Inspired by commitment.</p>
  </section>
</body>
</html>
```